BOLD & MINIMALIST DESIGN NEEDED

We want a very bold but minimalistic business card design that is impactful and utilizes both sides of the business card. Our current logo is included for your use.

We want bold fonts and good use of negative space. We don't want the logo to overpower the design.

Target Market(s)

Professionals who are building new commercial buildings.

Industry/Entity Type

Construction

Contact Information for Business Card

Name, Title, email, office phone, cell phone, website

Font styles to use
Serif
Sans Serif

Requirements
Must have
• Bold design!

```html
<!DOCTYPE html>
<html lang="en">
<head>
<meta charset="utf-8">
<title>Ridgeline Design + Build – Business Card</title>
<link href="https://fonts.googleapis.com/css2?family=Poppins:wght@400;500;700;800&display=swap" rel="stylesheet">
<style>
  :root {
    --backdrop: #262626;
    --card-dark: #232323;
    --card-dark-edge: #1b1b1b;
    --card-light: #f0f0f0;
    --ink: #222222;
    --ink-soft: #b8b8b8;
    --accent: #7cb82c;
    --white: #ffffff;
  }
  * { margin: 0; padding: 0; box-sizing: border-box; }
  html, body {
    width: 1200px;
    height: 576px;
    overflow: hidden;
    background: var(--backdrop);
    font-family: "Poppins", sans-serif;
  }
  .canvas {
    position: relative;
    width: 1200px;
    height: 576px;
  }
  .card {
    position: absolute;
    top: 139px;
    width: 482px;
    height: 292px;
    border-radius: 8px;
    overflow: hidden;
  }
  .card--front {
    left: 102px;
    background: linear-gradient(135deg, #2a2a2a 0%, var(--card-dark) 55%, var(--card-dark-edge) 100%);
  }
  .card--back {
    left: 596px;
    background: var(--card-light);
  }
  .front-wordmark {
    position: absolute;
    left: 48px;
    top: 146px;
    color: var(--white);
    font-weight: 800;
    font-size: 18px;
    letter-spacing: 0.04em;
    text-transform: uppercase;
  }
  .front-block {
    position: absolute;
    right: 0;
    top: 0;
    width: 160px;
    height: 292px;
    background: linear-gradient(90deg, #1c1c1c 0%, #3a3a3a 100%);
  }
  .holder-name {
    position: absolute;
    left: 30px;
    top: 30px;
    color: var(--accent);
    font-weight: 500;
    font-size: 21px;
  }
  .holder-title {
    position: absolute;
    left: 31px;
    top: 59px;
    color: var(--ink-soft);
    font-size: 10px;
  }
  .contact-list {
    position: absolute;
    left: 36px;
    top: 214px;
    list-style: none;
  }
  .contact-list li {
    display: flex;
    align-items: center;
    height: 16.5px;
    color: var(--ink);
    font-size: 12px;
  }
  .contact-list svg {
    width: 10px;
    height: 10px;
    margin-right: 7px;
    fill: var(--accent);
  }
  .back-wordmark {
    position: absolute;
    right: 30px;
    bottom: 36px;
    color: var(--ink);
    font-weight: 800;
    font-size: 15px;
    letter-spacing: 0.03em;
    text-transform: uppercase;
  }
</style>
</head>
<body>
<main class="canvas">
  <section class="card card--front">
    <p class="front-wordmark">Ridgeline Design + Build</p>
    <div class="front-block" role="img" aria-label="Dark tonal panel"></div>
  </section>

  <section class="card card--back">
    <h1 class="holder-name">Daniel Reyes</h1>
    <p class="holder-title">Director</p>
    <ul class="contact-list">
      <li>
        <svg viewBox="0 0 10 10" aria-hidden="true"><path d="M1 3c0-1 1-2 2-2h4c1 0 2 1 2 2v1H7V3H3v1H1zM2 5h6l1 4H1z"/></svg>
        555-201-0147
      </li>
      <li>
        <svg viewBox="0 0 10 10" aria-hidden="true"><path d="M0 2h10v6H0zM0 2l5 3.5L10 2v1L5 6.5 0 3z" fill-rule="evenodd"/></svg>
        daniel@ridgelinebuild.com
      </li>
      <li>
        <svg viewBox="0 0 10 10" aria-hidden="true"><circle cx="5" cy="5" r="4.5"/></svg>
        www.ridgelinebuild.com
      </li>
    </ul>
    <p class="back-wordmark">Ridgeline Design + Build</p>
  </section>
</main>
</body>
</html>
```